indépendant en tant que Massothérapeute et Préparateur Mental, j'ai besoin de ...

Massothérapeute et préparateur mental indépendant, je recherche une carte de visite sobre et dynamique, sans images liées au massage ou à la préparation mentale mais intégrant mon logo. Les couleurs que j'aime bien sont : Blanc, gris, anthracite, noir et jaune

Contact Information for Business Card

carte de préférence Horizontale
neutre qui puisse toucher le deux domaines Massothérapie et préparation mentale

Requirements
Must have
• mon projet doit intégrer au recto:
LOGO
Loïc Bardèze
078 513 26 48
info@loicbardeze.ch
et éventuellement www.loicbardeze.ch

et au verso les deux adresses:

Chemin des Ormilles 7B
1400 Yverdon-les-Bains

Route de la Gravière 9
1618 Valdormes

Should not have
• mon projet ne doit pas contenir d'image en liens avec le massage ni la préparation mentale.

```html
<!DOCTYPE html>
<html lang="fr">
<head>
<meta charset="utf-8">
<title>Carte de visite – Loïc Bardèze</title>
<link href="https://fonts.googleapis.com/css2?family=Rajdhani:wght@400;700&family=Roboto:wght@400&family=Montserrat:wght@500&display=swap" rel="stylesheet">
<style>
  :root {
    --backdrop: #8c8c8c;
    --card-white: #ffffff;
    --anthracite: #231f20;
    --ink: #1d1b1c;
    --text-grey: #4a4a4a;
    --silver: #b9adb0;
    --silver-dim: #6e6668;
  }
  html, body { margin: 0; padding: 0; overflow: hidden; }
  body { width: 1200px; height: 1200px; background: var(--backdrop); position: relative; }

  .card { position: absolute; left: 262px; width: 686px; box-sizing: border-box; }

  /* Recto */
  .card--front { top: 165px; height: 392px; background: var(--card-white); }
  .card--front::after {
    content: ""; position: absolute; left: 0; right: 0; bottom: 0; height: 14px; background: var(--anthracite);
  }
  .brand { position: absolute; right: 40px; top: 46px; display: flex; align-items: center; gap: 10px; }
  .brand__mark { width: 14px; height: 14px; background: var(--ink); }
  .brand__text { display: flex; flex-direction: column; align-items: flex-end; }
  .brand__name { font-family: "Rajdhani", sans-serif; font-weight: 700; font-size: 24px; line-height: 1; color: var(--ink); letter-spacing: 0.5px; }
  .brand__role { font-family: "Montserrat", sans-serif; font-weight: 500; font-size: 8px; color: var(--ink); letter-spacing: 0.6px; margin-top: 3px; }

  .name-row { position: absolute; left: 40px; right: 42px; top: 245px; display: flex; align-items: center; gap: 10px; }
  .name-row__name { font-family: "Rajdhani", sans-serif; font-size: 22px; color: var(--ink); white-space: nowrap; }
  .name-row__name strong { font-weight: 700; }
  .name-row__rule { flex: 1; height: 2px; background: var(--ink); }

  .contacts { position: absolute; left: 40px; top: 295px; margin: 0; padding: 0; list-style: none;
    font-family: "Roboto", sans-serif; font-size: 16px; color: var(--text-grey); line-height: 19.5px; }
  .contacts li { display: flex; align-items: center; gap: 9px; }
  .contacts svg { width: 12px; height: 12px; fill: var(--ink); flex: none; }

  .addresses { position: absolute; right: 40px; top: 272px; text-align: right;
    font-family: "Roboto", sans-serif; font-size: 16px; color: var(--text-grey); line-height: 19px; }
  .addresses p { margin: 0 0 8px; }

  /* Verso */
  .card--back { top: 653px; height: 391px; background: var(--anthracite); display: flex; align-items: center; justify-content: center; }
  .back-brand { display: flex; align-items: center; gap: 16px; }
  .back-brand__mark { width: 22px; height: 22px; background: var(--silver); }
  .back-brand__name { font-family: "Rajdhani", sans-serif; font-weight: 700; font-size: 40px; line-height: 1; color: var(--silver); letter-spacing: 1px; }
  .back-brand__role { font-family: "Montserrat", sans-serif; font-weight: 500; font-size: 10px; color: var(--silver-dim); letter-spacing: 0.8px; margin-top: 4px; }
</style>
</head>
<body>

<section class="card card--front" aria-label="Recto">
  <div class="brand">
    <span class="brand__mark"></span>
    <div class="brand__text">
      <span class="brand__name">Loïc Bardèze</span>
      <span class="brand__role">MASSOTHÉRAPEUTE / PRÉPARATEUR MENTAL</span>
    </div>
  </div>

  <div class="name-row">
    <span class="name-row__name">Loïc <strong>BARDÈZE</strong></span>
    <span class="name-row__rule"></span>
  </div>

  <ul class="contacts">
    <li><svg viewBox="0 0 24 24"><path d="M6.6 10.8a15 15 0 0 0 6.6 6.6l2.2-2.2c.3-.3.7-.4 1-.2 1.1.4 2.3.6 3.6.6.6 0 1 .4 1 1V20c0 .6-.4 1-1 1A17 17 0 0 1 3 4c0-.6.4-1 1-1h3.5c.6 0 1 .4 1 1 0 1.3.2 2.5.6 3.6.1.3 0 .7-.2 1z"/></svg>078 513 26 48</li>
    <li><svg viewBox="0 0 24 24"><path d="M2 5h20v14H2z"/><path d="M2 6l10 7 10-7V5H2z" fill="#fff"/></svg>info@loicbardeze.ch</li>
    <li><svg viewBox="0 0 24 24"><circle cx="12" cy="12" r="10"/><path d="M2 12h20M12 2c3 3 3 17 0 20M12 2c-3 3-3 17 0 20" stroke="#fff" stroke-width="1.5" fill="none"/></svg>www.loicbardeze.ch</li>
  </ul>

  <div class="addresses">
    <p>Route de la Gravière 9<br>1618 Valdormes</p>
    <p>Chemin des Ormilles 7B<br>1422 Montrevaz-le-Lac</p>
  </div>
</section>

<section class="card card--back" aria-label="Verso">
  <div class="back-brand">
    <span class="back-brand__mark"></span>
    <div>
      <div class="back-brand__name">Loïc Bardèze</div>
      <div class="back-brand__role">MASSOTHÉRAPEUTE / PRÉPARATEUR MENTAL</div>
    </div>
  </div>
</section>

</body>
</html>
```